Valderons Business Card

Business card for philanthropic organization

Industry/Entity Type

Business

Contact Information for Business Card

Need a very ELEGANT, sober, embossed, formal business card... it should transmit CREDIBILITY. Not looking for a "fun card". would like white, grays or black designs.

Font styles to use
Script

Requirements
Must have
• Embossed look

```html
<!DOCTYPE html>
<html lang="en">
<head>
<meta charset="utf-8">
<title>Valderons Business Card</title>
<link href="https://fonts.googleapis.com/css2?family=Great+Vibes&family=Open+Sans:wght@400;600&display=swap" rel="stylesheet">
<style>
  :root {
    --backdrop: #a9a9a9;
    --card: #f7f7f6;
    --card-edge: #e9e9e8;
    --ink-strong: #4a4a4a;
    --ink: #6b6b6b;
    --ink-soft: #8c8c8c;
    --raise-light: rgba(255,255,255,0.95);
    --raise-dark: rgba(0,0,0,0.28);
  }
  html, body {
    margin: 0;
    width: 1200px;
    height: 881px;
    overflow: hidden;
    background: var(--backdrop);
    font-family: "Open Sans", sans-serif;
  }
  .business-card {
    position: absolute;
    left: 160px;
    top: 190px;
    width: 880px;
    height: 500px;
    background: radial-gradient(ellipse at 30% 20%, #fdfdfc 0%, var(--card) 55%, var(--card-edge) 100%);
    box-shadow: 0 14px 30px rgba(0,0,0,0.25), inset 0 0 0 1px rgba(255,255,255,0.7);
  }
  .embossed {
    text-shadow: -1px -1px 0 var(--raise-light), 1px 1px 1px var(--raise-dark);
  }
  .brand-mark {
    position: absolute;
    left: 150px;
    top: 70px;
    display: flex;
    align-items: center;
    gap: 14px;
  }
  .brand-mark .dot {
    width: 22px;
    height: 22px;
    border-radius: 50%;
    background: var(--ink-soft);
  }
  .brand-mark .name {
    font-size: 34px;
    font-weight: 600;
    color: var(--ink-soft);
  }
  .postal-address {
    position: absolute;
    left: 70px;
    bottom: 70px;
    font-size: 21px;
    line-height: 1.3;
    color: var(--ink);
  }
  .holder {
    position: absolute;
    right: 70px;
    bottom: 60px;
    text-align: right;
  }
  .holder-name {
    font-family: "Great Vibes", cursive;
    font-size: 44px;
    font-weight: 400;
    line-height: 1;
    color: var(--ink-strong);
    margin: 0 0 6px;
  }
  .holder-title {
    font-size: 22px;
    font-weight: 600;
    line-height: 1.2;
    text-transform: uppercase;
    letter-spacing: 0.04em;
    color: var(--ink);
    margin: 0 0 16px;
  }
  .contact-list {
    list-style: none;
    margin: 0;
    padding: 0;
    font-size: 20px;
    line-height: 1.35;
    color: var(--ink);
  }
  .contact-list li {
    display: flex;
    justify-content: flex-end;
    align-items: center;
    gap: 12px;
  }
  .contact-list svg { width: 18px; height: 18px; flex: none; }
</style>
</head>
<body>
  <div class="business-card">
    <div class="brand-mark">
      <span class="dot"></span>
      <span class="name">Valderons</span>
    </div>

    <div class="postal-address embossed">
      P.O. Box 0912-04518<br>
      Panama, Republic of Panama
    </div>

    <div class="holder">
      <h1 class="holder-name embossed">Mateo Calderas</h1>
      <p class="holder-title embossed">Al Noor Valderons<br>Potentate 2017</p>
      <ul class="contact-list embossed">
        <li>+(507)-6200-4817
          <svg viewBox="0 0 20 20" aria-hidden="true"><circle cx="10" cy="10" r="10" fill="#8c8c8c"/><path d="M6 5.5h2.2l1 2.5-1.3 1a6 6 0 0 0 3.1 3.1l1-1.3 2.5 1v2.2c-4.8.4-8.9-3.7-8.5-8.5z" fill="#fff"/></svg>
        </li>
        <li>mcalderas@mailbox.example
          <svg viewBox="0 0 20 20" aria-hidden="true"><circle cx="10" cy="10" r="10" fill="#8c8c8c"/><rect x="5" y="6.5" width="10" height="7" fill="#fff"/><path d="M5 6.5l5 4 5-4" fill="none" stroke="#8c8c8c" stroke-width="1"/></svg>
        </li>
        <li>www.mateocalderas.example
          <svg viewBox="0 0 20 20" aria-hidden="true"><circle cx="10" cy="10" r="10" fill="#8c8c8c"/><circle cx="10" cy="10" r="5" fill="none" stroke="#fff" stroke-width="1.2"/><path d="M5 10h10M10 5c-2.5 3-2.5 7 0 10M10 5c2.5 3 2.5 7 0 10" fill="none" stroke="#fff" stroke-width="1"/></svg>
        </li>
      </ul>
    </div>
  </div>
</body>
</html>
```